Korvath Supply Website Redesign

Currently korvathsupply.example is focussed on fulfillment and transport from various products in the BBQ segment. However, no we want to update our business activities to Product Development, Brand Development, Online Positioning, Logistics & Aftersales, and Promotional BBQs. We will be a business for Outdoor Leisure Development from A to Z.

Therefore, we need a brand new website. The colours of the current website may be the same. However, i'd like to keep it clean. More white and use blue and green as accent colours. It is a business to business organization so the website should be looking formal and corporate. However we sell fun products so not too formal and corporate.

Pages we need; Home, About, Contact, Our Services (+ page per service) a place to share our news/blogs.

I have added some sort of mock up of an idea. However it needs some finetuning.

Target Market(s)

Businesses

Industry/Entity Type

Corporate/Logistics/Marketing

Coding

Coded - Design and coding required

Colors

Designer to choose colors to be used in the design.

Requirements
Must have
• Show clear distinguishing of the different services we provide (Product Development, Brand Development, Online Positioning, Logistics & Aftersales and Promotional BBQs). Every service should have its own page too. Besides, I would like to have a blog page to share relevant content.
Nice to have
• Show that we are the expert in Outdoor LEisure Development from A to Z
Should not have
• Be too informal. It may be semi-formal

```html
<!DOCTYPE html>
<html lang="en">
<head>
<meta charset="utf-8">
<title>Korvath Supply – Outdoor Leisure Development</title>
<link href="https://fonts.googleapis.com/css2?family=Lato:wght@400;700&family=Raleway:wght@800;900&display=swap" rel="stylesheet">
<style>
:root{
  --navy:#04182a;
  --teal:#355b66;
  --teal-dark:#2f5560;
  --nav-active:#3d6e6a;
  --green:#3a9c3e;
  --green-light:#86c98a;
  --hero-green:#3aa13f;
  --ink:#1c1c1c;
  --muted:#6c6c6c;
  --date:#3a9c3e;
  --white:#ffffff;
  --line:#d6dbe0;
}
*{box-sizing:border-box;margin:0;padding:0}
html,body{width:1200px;height:3286px;overflow:hidden;background:var(--white)}
body{font-family:'Lato',sans-serif;color:var(--ink)}
.page{position:relative;width:1200px;height:3286px;overflow:hidden}
.abs{position:absolute}

/* header */
.site-header{position:absolute;left:0;top:0;width:1200px;height:91px;background:var(--white);z-index:5}
.brand{position:absolute;left:143px;top:22px;display:flex;align-items:center;gap:12px}
.brand-dot{width:36px;height:36px;border-radius:50%;background:var(--teal)}
.brand-name{font-family:'Raleway',sans-serif;font-weight:900;font-size:30px;color:var(--teal-dark)}
.main-nav{position:absolute;left:663px;top:0;display:flex;height:91px}
.main-nav a{display:flex;align-items:center;height:91px;padding:0 17px;font-size:18px;color:var(--ink);text-decoration:none}
.main-nav a.is-active{background:var(--nav-active);color:var(--white);padding:0 13px}

/* hero */
.hero-bg{position:absolute;left:0;top:91px;width:1200px;height:600px}
.hero-globe{position:absolute;left:660px;top:91px;width:540px;height:560px;background:radial-gradient(circle at 62% 45%,#3f9ee8 0%,#1d5fa6 28%,rgba(4,24,42,0) 62%)}
.hero-title{position:absolute;left:143px;top:208px;font-family:'Raleway',sans-serif;font-weight:900;font-size:62px;line-height:70px;color:var(--white)}
.hero-title .accent{color:var(--hero-green)}

/* service circles */
.service{position:absolute;border-radius:50%;display:flex;flex-direction:column;align-items:center;color:var(--white);text-align:center}
.service-icon{margin-top:38px}
.service-label{font-size:23px;font-weight:700;line-height:29px;margin-top:30px}
.svc-product{left:36px;top:591px;width:298px;height:298px;background:var(--teal)}
.svc-brand{left:297px;top:591px;width:298px;height:298px;background:var(--green)}
.svc-online{left:556px;top:591px;width:298px;height:298px;background:var(--green-light)}
.svc-logistics{left:822px;top:570px;width:332px;height:332px;background:var(--teal)}
.svc-logistics .service-icon{margin-top:38px}
.svc-logistics .service-label{margin-top:10px;line-height:31px}
.service-text{font-size:13.5px;line-height:22px;margin-top:14px;width:225px}
.service-more{margin-top:10px}

/* difference */
.difference-band{position:absolute;left:0;top:1050px;width:1200px;height:260px;background:linear-gradient(180deg,#ffffff 0%,#f2f5f8 60%,#e9edf2 100%)}
.section-title{position:absolute;left:0;width:1200px;text-align:center;font-family:'Raleway',sans-serif;font-weight:900;font-size:62px;color:var(--teal-dark)}
.difference-text{position:absolute;left:190px;top:1103px;width:820px;text-align:center;font-size:15px;line-height:29px;color:#4a4a4a}
.team-photo{position:absolute;left:0;top:1310px;width:1200px;height:668px;background:linear-gradient(120deg,#c9d6e3 0%,#5f7fa8 35%,#2b4c86 60%,#d8dfe6 100%)}

/* news */
.news-bg{position:absolute;left:0;top:2200px;width:1200px;height:700px;background:linear-gradient(180deg,#ffffff 0%,#f1f3f6 100%)}
.news-card{position:absolute;background:var(--white);border:1.5px solid var(--line);border-radius:22px;overflow:hidden}
.news-media{position:absolute}
.news-body{position:absolute}
.news-date{font-size:13px;color:var(--date)}
.news-heading{font-size:18px;font-weight:400;line-height:25px;color:var(--ink);margin-top:14px}
.news-excerpt{font-size:11.5px;line-height:21.5px;color:var(--muted);margin-top:12px}
.read-more{display:block;font-size:16px;font-weight:700;color:var(--teal);text-decoration:none}
.card-feature{left:140px;top:2248px;width:298px;height:510px}
.card-feature .news-media{left:3px;top:3px;width:289px;height:222px;border-radius:20px 20px 40px 40px;background:linear-gradient(180deg,#1d3b8a 0%,#4463b8 45%,#9aa3b0 100%)}
.card-feature .news-body{left:22px;top:250px;width:250px}
.card-feature .read-more{margin-top:36px}
.card-row{left:454px;width:605px;height:248px}
.card-row .news-media{left:3px;top:3px;width:236px;height:240px;border-radius:20px 40px 40px 20px}
.card-row .news-body{left:270px;top:22px;width:300px}
.card-row .read-more{margin-top:30px;margin-left:3px}
.card-top{top:2248px}
.card-top .news-media{background:linear-gradient(180deg,#6f86a8 0%,#aab5c4 45%,#4a5566 100%)}
.card-bottom{top:2509px}
.card-bottom .news-media{background:linear-gradient(135deg,#5d6b5c 0%,#c2c9c1 50%,#2f3a46 100%)}

/* footer */
.site-footer{position:absolute;left:0;top:2850px;width:1200px;height:436px}
.footer-heading{position:absolute;top:3034px;font-size:23px;font-weight:700;color:var(--white)}
.footer-list{position:absolute;top:3085px;list-style:none}
.footer-list li{font-size:14px;line-height:27.5px;color:var(--white)}
.footer-list a{color:var(--white);text-decoration:none}
.footer-brand{position:absolute;left:737px;top:3048px;display:flex;align-items:center;gap:16px}
.footer-brand .brand-dot{width:58px;height:58px}
.footer-brand .brand-name{font-size:42px;color:var(--teal)}
.legal{position:absolute;left:0;top:3226px;width:1200px;text-align:center;font-size:14px;color:var(--white)}
.legal a{color:var(--white);text-decoration:none}
</style>
</head>
<body>
<div class="page">

  <header class="site-header">
    <div class="brand"><span class="brand-dot"></span><span class="brand-name">Korvath Supply</span></div>
    <nav class="main-nav">
      <a href="#" class="is-active">Home</a>
      <a href="#">About</a>
      <a href="#">Our Services</a>
      <a href="#">Contact</a>
    </nav>
  </header>

  <svg class="hero-bg" viewBox="0 91 1200 600" width="1200" height="600" aria-hidden="true">
    <path d="M0 91 H1200 V620 Q600 800 0 618 Z" fill="#04182a"/>
    <path d="M900 700 Q1080 680 1200 620 V650 Q1080 700 920 712 Z" fill="#3a9c3e"/>
    <path d="M0 618 Q30 628 60 640 L0 630 Z" fill="#3a9c3e"/>
  </svg>
  <div class="hero-globe" role="img" aria-label="Glowing digital globe with network lines"></div>

  <h1 class="hero-title">OUTDOOR<br><span class="accent">LEISURE</span><br>DEVELOPMENT<br><span class="accent">FROM ATO Z</span></h1>

  <section class="service svc-product">
    <svg class="service-icon" width="64" height="130" viewBox="0 0 64 130" aria-hidden="true">
      <circle cx="38" cy="10" r="8" fill="none" stroke="#fff" stroke-width="3"/>
      <circle cx="22" cy="22" r="6" fill="none" stroke="#fff" stroke-width="3"/>
      <circle cx="36" cy="32" r="5" fill="none" stroke="#fff" stroke-width="3"/>
      <path d="M24 44 H40 V72 L60 116 Q62 122 56 122 H8 Q2 122 4 116 L24 72 Z" fill="#fff"/>
    </svg>
    <div class="service-label">Product<br>Development</div>
  </section>

  <section class="service svc-brand">
    <svg class="service-icon" width="120" height="130" viewBox="0 0 120 130" aria-hidden="true">
      <path d="M8 2 H112 L118 50 Q110 62 100 50 Q90 62 80 50 Q70 62 60 50 Q50 62 40 50 Q30 62 20 50 Q10 62 2 50 Z" fill="#fff"/>
      <path d="M26 6 L22 48 M46 6 L44 48 M60 6 V48 M74 6 L76 48 M94 6 L98 48" stroke="#3a9c3e" stroke-width="5"/>
      <rect x="10" y="62" width="100" height="56" fill="none" stroke="#fff" stroke-width="8"/>
      <rect x="6" y="116" width="108" height="8" fill="#fff"/>
    </svg>
    <div class="service-label">Brand<br>Development</div>
  </section>

  <section class="service svc-online">
    <svg class="service-icon" width="110" height="130" viewBox="0 0 110 130" aria-hidden="true">
      <rect x="4" y="38" width="102" height="64" fill="none" stroke="#fff" stroke-width="6"/>
      <rect x="40" y="102" width="30" height="10" fill="#fff"/>
      <rect x="28" y="112" width="54" height="6" fill="#fff"/>
      <circle cx="55" cy="38" r="34" fill="#fff"/>
      <g fill="none" stroke="#86c98a" stroke-width="3">
        <ellipse cx="55" cy="38" rx="14" ry="34"/>
        <line x1="55" y1="4" x2="55" y2="72"/>
        <line x1="21" y1="38" x2="89" y2="38"/>
        <path d="M26 22 H84 M26 54 H84"/>
      </g>
    </svg>
    <div class="service-label">Online<br>Positioning</div>
  </section>

  <section class="service svc-logistics">
    <svg class="service-icon" width="80" height="60" viewBox="0 0 80 60" aria-hidden="true">
      <path d="M4 22 L36 4 L68 22 V56 H4 Z" fill="none" stroke="#fff" stroke-width="4"/>
      <rect x="18" y="28" width="14" height="6" fill="#fff"/>
      <rect x="18" y="37" width="22" height="6" fill="#fff"/>
      <rect x="18" y="46" width="22" height="6" fill="#fff"/>
      <path d="M44 30 H62 L74 42 V54 H44 Z" fill="#fff"/>
      <circle cx="52" cy="56" r="4" fill="#fff"/>
      <circle cx="68" cy="56" r="4" fill="#fff"/>
    </svg>
    <div class="service-label">Logistics<br>&amp; Aftersales</div>
    <p class="service-text">Lorem ipsum dolor sit amet, consectetur adipiscing elit, sed do eiusmod tempor incididunt ut labore et dolorea aliqua</p>
    <svg class="service-more" width="20" height="12" viewBox="0 0 20 12" aria-hidden="true"><path d="M2 2 L10 10 L18 2" fill="none" stroke="#fff" stroke-width="3"/></svg>
  </section>

  <div class="difference-band" aria-hidden="true"></div>
  <h2 class="section-title" style="top:996px">WE MAKE THE DIFFERENCE</h2>
  <p class="difference-text">Lorem ipsum dolor sit amet, consectetur adipiscing elit, sed do eiusmod tempor incididunt ut labore et dolore magna aliqua. Quis ipsum suspendisse ultrices gravida. Risus commodo viverra maecenas accumsan lacus vel facilisisorem ipsum dolor sit amet, consectetur adipiscing elit, sed do eiusmod tempor incididunt ut labore et dolore magna aliquuis ipsum suspendisse gravida. Risus commodo viverra maecenas accumsan lacus vel facit, cod do eiusmod tempor incididunt ut labore et dolore magna a suspendisse ultrices gravida. Risus commodo viverra maecenas accumsan lacus vel facilisis.</p>

  <div class="team-photo" role="img" aria-label="Photo of a team of four colleagues leaning over a table reviewing plans in an office"></div>

  <div class="news-bg" aria-hidden="true"></div>
  <h2 class="section-title" style="top:2106px">LATEST NEWS</h2>

  <article class="news-card card-feature">
    <div class="news-media" role="img" aria-label="Photo of a large warehouse with blue shelving and trucks"></div>
    <div class="news-body">
      <div class="news-date">Aug,2019</div>
      <h3 class="news-heading">Sed ut perspiciatis unde omnis iste natus</h3>
      <p class="news-excerpt">Ut enim ad minima veniam, quis nostreierci tationem ullam corporis suscipit laboriosan isi ut aliquid ex ea commodi eprehenderitq ui in ea voluptate velit .</p>
      <a href="#" class="read-more">READ MORE</a>
    </div>
  </article>

  <article class="news-card card-row card-top">
    <div class="news-media" role="img" aria-label="Photo of a cargo port with a crane, trucks and an airplane overhead"></div>
    <div class="news-body">
      <div class="news-date">Aug,2019</div>
      <h3 class="news-heading">Sed ut perspiciatis unde omnis iste natus error</h3>
      <p class="news-excerpt">Ut enim ad minima veniam, quis nostreierci tationem ullam corporis suscipit laboriosan isi ut aliquid ex ea eprehenderitq utate velit .</p>
      <a href="#" class="read-more">READ MORE</a>
    </div>
  </article>

  <article class="news-card card-row card-bottom">
    <div class="news-media" role="img" aria-label="Photo of hands working with a tablet and pen at a desk"></div>
    <div class="news-body">
      <div class="news-date">Aug,2019</div>
      <h3 class="news-heading">Sed ut perspiciatis unde omnis iste natus error</h3>
      <p class="news-excerpt">Ut enim ad minima veniam, quis nostreierci tationem ullam corporis suscipit laboriosan isi ut aliquid ex ea eprehenderitq utate velit .</p>
      <a href="#" class="read-more">READ MORE</a>
    </div>
  </article>

  <svg class="site-footer" viewBox="0 2850 1200 436" width="1200" height="436" aria-hidden="true">
    <path d="M0 3050 Q600 2630 1200 3050 V3286 H0 Z" fill="#3a9c3e"/>
    <path d="M0 3070 Q600 2654 1200 3070 V3286 H0 Z" fill="#04182a"/>
  </svg>

  <h4 class="footer-heading" style="left:143px">SITEMAP</h4>
  <ul class="footer-list" style="left:145px">
    <li><a href="#">Home</a></li>
    <li><a href="#">About</a></li>
    <li><a href="#">Our services</a></li>
    <li><a href="#">Contact</a></li>
    <li><a href="#">Blog</a></li>
  </ul>

  <h4 class="footer-heading" style="left:399px">CONTACT</h4>
  <ul class="footer-list" style="left:401px">
    <li>Lindenhof 12</li>
    <li>4800 AB, Ellenstad The Netherlands</li>
  </ul>

  <div class="footer-brand"><span class="brand-dot"></span><span class="brand-name">Korvath Supply</span></div>

  <p class="legal">© 2021 Korvath Supply.All rights reserved &nbsp;|&nbsp; <a href="#">Privacy</a> &nbsp;|&nbsp; <a href="#">Terms of Use</a></p>

</div>
</body>
</html>
```